Redesign current business card for food company

i would like to redesign my business card. our company is food company, our product range from chips, juices, milk and etc (mostly dried food stuff).
I want o keep same logo but , the rest is open to new design.
you can check at our website about our company www.orvelpantry.com

Target Market(s)

most of food company

Industry/Entity Type

Business

Contact Information for Business Card

I want to keep more to blue color...

Colors
3176b5
abd036

Requirements
Must have
• our old logo
Nice to have
• we do not mind to have nice material on bus card in order to accomplish nice design. for example: using spot uv, embossed and etc.

```html
<!DOCTYPE html>
<html lang="en">
<head>
<meta charset="utf-8">
<title>Orvel Business Card</title>
<link rel="stylesheet" href="https://fonts.googleapis.com/css2?family=Montserrat:wght@400;500;700;800&display=swap">
<style>
  :root {
    --indigo: #34338f;
    --cyan: #16a9c4;
    --white: #ffffff;
    --backdrop: #e9eaee;
    --shadow: rgba(20, 20, 40, 0.18);
  }
  * { box-sizing: border-box; margin: 0; padding: 0; }
  html, body {
    width: 1200px; height: 900px; overflow: hidden;
    background: var(--backdrop);
    font-family: "Montserrat", Arial, sans-serif;
  }
  .sheet {
    width: 1200px; height: 900px;
    display: flex; flex-direction: column; align-items: center; justify-content: center;
    gap: 30px;
  }
  .card {
    position: relative;
    width: 720px; height: 411px;
    border-radius: 22px;
    overflow: hidden;
    background: var(--white);
    box-shadow: 0 8px 24px var(--shadow);
  }
  /* Front */
  .front-brand {
    position: absolute; left: 0; right: 0; top: 120px;
    text-align: center;
    font-weight: 800; font-size: 120px; letter-spacing: -3px;
    color: var(--indigo); line-height: 1;
  }
  .front-web {
    position: absolute; left: 0; right: 0; bottom: 48px;
    text-align: center;
    font-weight: 500; font-size: 19px; letter-spacing: 0.5px;
    color: var(--indigo);
  }
  /* Back */
  .back-shapes { position: absolute; inset: 0; }
  .back-brand {
    position: absolute; left: 50px; top: 130px;
    font-weight: 800; font-size: 100px; letter-spacing: -3px;
    color: var(--white); line-height: 1;
  }
  .contact {
    position: absolute; right: 52px; top: 78px;
    text-align: right;
    color: var(--indigo);
  }
  .contact-name { font-weight: 700; font-size: 20px; letter-spacing: 0.3px; line-height: 24px; }
  .contact-title { font-weight: 500; font-size: 15px; color: var(--cyan); line-height: 20px; }
  .contact-company, .contact-address { font-size: 13px; font-weight: 400; line-height: 18px; }
  .contact-company { margin-top: 4px; }
  .contact-lines { list-style: none; margin-top: 12px; }
  .contact-lines li {
    font-size: 15px; font-weight: 500; line-height: 23px;
    display: flex; justify-content: flex-end; align-items: center; gap: 8px;
  }
  .contact-lines svg { width: 13px; height: 13px; flex: none; }
  .web-accent { color: var(--cyan); font-weight: 700; }
</style>
</head>
<body>
<main class="sheet">
  <section class="card card-front">
    <div class="front-brand">orvel</div>
    <div class="front-web">www.orvelpantry.com</div>
  </section>

  <section class="card card-back">
    <svg class="back-shapes" viewBox="0 0 720 411" width="720" height="411" aria-hidden="true">
      <path d="M0 0 H440 C370 70 300 230 270 411 H0 Z" fill="var(--indigo)"/>
      <path d="M468 -4 C398 70 328 230 297 415" fill="none" stroke="var(--cyan)" stroke-width="10"/>
      <path d="M694 0 H720 V200 H712 Q694 200 694 182 Z" fill="var(--indigo)"/>
    </svg>
    <div class="back-brand">orvel</div>
    <div class="contact">
      <div class="contact-name">Daniel Hartono</div>
      <div class="contact-title">President</div>
      <div class="contact-company">Orvel Enterprises Corp.</div>
      <div class="contact-address">2840 W Ridge Ave. Fairview CA 91802</div>
      <ul class="contact-lines">
        <li>555 014 2230
          <svg viewBox="0 0 14 14"><path d="M3 1 L5.5 1 L6.5 4 L5 5.2 Q6.3 8 8.8 9 L10 7.5 L13 8.5 L13 11 Q12 13 9.5 12.5 Q3 10.5 1.5 4.5 Q1 2 3 1Z" fill="var(--cyan)"/></svg>
        </li>
        <li>555 014 2231
          <svg viewBox="0 0 14 14"><rect x="1" y="5" width="12" height="6" rx="1.5" fill="var(--cyan)"/><rect x="3.5" y="1.5" width="7" height="4" fill="var(--cyan)"/><rect x="3.5" y="9" width="7" height="4" fill="var(--white)" stroke="var(--cyan)" stroke-width="1.2"/></svg>
        </li>
        <li>555 018 7742
          <svg viewBox="0 0 14 14"><rect x="3.5" y="1" width="7" height="12" rx="1.5" fill="none" stroke="var(--cyan)" stroke-width="1.5"/><circle cx="7" cy="10.6" r="0.9" fill="var(--cyan)"/></svg>
        </li>
        <li>daniel@orvelpantry.com
          <svg viewBox="0 0 14 14"><rect x="1" y="3" width="12" height="8.5" rx="1" fill="none" stroke="var(--cyan)" stroke-width="1.4"/><path d="M1.5 3.5 L7 8 L12.5 3.5" fill="none" stroke="var(--cyan)" stroke-width="1.4"/></svg>
        </li>
        <li><span>www.<span class="web-accent">orvelpantry</span>.com</span>
          <svg viewBox="0 0 14 14"><circle cx="7" cy="7" r="5.8" fill="none" stroke="var(--cyan)" stroke-width="1.3"/><ellipse cx="7" cy="7" rx="2.6" ry="5.8" fill="none" stroke="var(--cyan)" stroke-width="1.1"/><path d="M1.2 7 H12.8" stroke="var(--cyan)" stroke-width="1.1"/></svg>
        </li>
      </ul>
    </div>
  </section>
</main>
</body>
</html>
```